Landingpage Design X-Mas Invitation

Every year we invite customers to a special X-Mas Apéro. Since we are an IT-Company we handle the registration process by a landingpage. For this we need a design for the event 2016. The content will be the same as 2015 (you will finde the design attached from last year. There will be an additional job for creating the E-Mail.

Target Market(s)

Customers of IT Company, medium Companys in Central Switzerland

Industry/Entity Type

It Company

Number of Pages Required

1 page

Requirements
Must have
• Christmas Style

```html
<!DOCTYPE html>
<html lang="de">
<head>
<meta charset="utf-8">
<title>Lichtwerk IT Solutions – Weihnachts-Apéro</title>
<link rel="stylesheet" href="https://fonts.googleapis.com/css2?family=Source+Sans+3:wght@300;400;600&display=swap">
<style>
  :root{
    --brand-red:#c8402e;
    --brand-red-dark:#b5331f;
    --sky-light:#eef7e2;
    --sky-green:#9dd05a;
    --panel-top:#7cbb2a;
    --panel-bottom:#3e8a12;
    --white:#ffffff;
    --grey-line:#d3d3d3;
    --footer-top:#dc6a52;
    --footer-bottom:#c23b28;
  }
  *{box-sizing:border-box;margin:0;padding:0}
  html,body{width:928px;height:1200px;overflow:hidden;background:var(--white)}
  body{font-family:"Source Sans 3","Source Sans Pro",sans-serif;position:relative}
  .page{position:relative;width:928px;height:1200px;overflow:hidden}

  .sky{position:absolute;left:0;top:0;width:928px;height:560px;
    background:linear-gradient(100deg,var(--sky-light) 10%,#d3ecb2 55%,var(--sky-green) 100%)}
  .clouds{position:absolute;left:0;top:0;width:928px;height:560px}

  .brand{position:absolute;top:28px;left:0;width:928px;text-align:center;
    color:var(--brand-red);font-weight:600;font-size:52px;line-height:1;letter-spacing:-0.5px}
  .brand-sub{display:block;font-size:15px;letter-spacing:1px;margin-top:3px}

  .garland{position:absolute;left:0;top:0;width:104px;height:128px;
    background:radial-gradient(circle at 0 0,#3f7d2a 0,#5c9a3a 55%,rgba(92,154,58,0) 75%)}
  .santa{position:absolute;left:140px;top:172px;width:185px;height:200px;border-radius:48% 48% 42% 42%;
    background:linear-gradient(180deg,#e9523f 0%,#d8362a 55%,#b92a20 100%)}

  .tilt{position:absolute;color:#e85a48;font-weight:300;font-size:20px;line-height:1.35;
    text-transform:uppercase;white-space:nowrap;transform-origin:left top}
  .tilt-title{left:68px;top:112px;transform:rotate(40deg);text-align:center}
  .tilt-date{left:342px;top:282px;transform:rotate(-40deg);text-align:right}
  .tilt-venue{left:38px;top:485px;transform:rotate(-25deg);text-align:right}
  .tilt-brand{left:284px;top:440px;transform:rotate(-25deg);color:var(--brand-red);
    font-weight:600;font-size:30px;text-transform:none;line-height:1}

  .intro{position:absolute;left:498px;top:226px;width:395px;color:var(--brand-red);
    font-size:23px;line-height:36px;font-weight:400}

  .signup{position:absolute;left:36px;top:549px;width:856px;height:403px;border-radius:2px;
    background:linear-gradient(180deg,var(--panel-top),var(--panel-bottom))}
  .signup h2{position:absolute;top:34px;color:var(--white);font-weight:400;font-size:31px}
  .col-left{left:67px}.col-right{left:451px}
  .field{position:absolute;width:333px;height:43px;border:0;background:var(--white);
    padding:0 23px;font-family:inherit;font-size:18px;color:var(--brand-red)}
  .field::placeholder{color:var(--brand-red)}
  .btn{position:absolute;top:302px;height:48px;font-family:inherit;font-size:18px;
    color:var(--white);text-transform:uppercase;cursor:pointer}
  .btn-guest{left:180px;width:240px;background:transparent;border:2px solid rgba(255,255,255,.35);border-radius:2px}
  .btn-send{left:436px;width:239px;border:0;border-radius:2px;
    background:linear-gradient(180deg,#e2604a,var(--brand-red-dark))}

  .partners{position:absolute;left:0;top:1013px;width:928px;height:57px}
  .partner{position:absolute;top:0;width:160px;height:57px;border:1px solid var(--grey-line);
    display:flex;align-items:center;justify-content:center}
  .partner span{display:block;width:90px;height:18px;border-radius:3px;background:#e6e6e6}
  .arrow{position:absolute;top:16px;width:24px;height:24px}

  .footer{position:absolute;left:0;top:1121px;width:928px;height:79px;
    background:linear-gradient(180deg,var(--footer-top),var(--footer-bottom));
    color:var(--white);font-size:16px;display:flex;align-items:center;justify-content:center}
</style>
</head>
<body>
<div class="page">
  <div class="sky"></div>
  <svg class="clouds" viewBox="0 0 928 560" aria-hidden="true">
    <path fill="#ffffff" d="M0,174 C40,120 90,100 150,104 C260,110 380,120 440,162 C470,120 520,110 560,116 C620,124 670,160 684,186 C700,150 730,136 760,139 C780,142 795,160 800,174 C820,130 860,110 900,114 C915,116 925,120 928,128 L928,560 L0,560 Z"/>
  </svg>

  <header class="brand">Lichtwerk <span class="brand-sub">IT SOLUTIONS</span></header>

  <div class="garland" role="img" aria-label="Tannenzweig mit goldener Schleife und Kugelkette"></div>
  <div class="santa" role="img" aria-label="Fröhlicher Weihnachtsmann mit ausgebreiteten Armen"></div>

  <div class="tilt tilt-title">Lichtwerk<br>Weihnachts<br>Apéro</div>
  <div class="tilt tilt-date">17. Dezember 2016<br>17 – 20 Uhr</div>
  <div class="tilt tilt-venue">Panoramalounge<br>Talackerweg 12<br>Luzern</div>
  <div class="tilt tilt-brand">Lichtwerk</div>

  <p class="intro">Ob Sie den ganzen Abend bleiben oder nur kurz nach dem Weihnachts-Shopping vorbeischauen, ist ganz Ihnen überlassen. Wir freuen uns sehr, wenn Sie uns die Gelegenheit geben, Ihnen mit dieser Einladung für die erfolgreiche Zusammenarbeit herzlichst zu danken.</p>

  <form class="signup">
    <h2 class="col-left">Ihre Anmeldung</h2>
    <h2 class="col-right">Ihre Begleitperson</h2>
    <input class="field" style="left:70px;top:101px" type="email" placeholder="Ihre E-Mail-Adresse">
    <input class="field" style="left:70px;top:159px" type="text" placeholder="Vorname">
    <input class="field" style="left:70px;top:217px" type="text" placeholder="Nachname">
    <input class="field" style="left:454px;top:101px" type="text" placeholder="Vorname">
    <input class="field" style="left:454px;top:159px" type="text" placeholder="Nachname">
    <input class="field" style="left:454px;top:217px" type="text" placeholder="Firma (Optional)">
    <button class="btn btn-guest" type="button">Weitere Begleitperson</button>
    <button class="btn btn-send" type="submit">Absenden</button>
  </form>

  <section class="partners" aria-label="Partner">
    <svg class="arrow" style="left:31px" viewBox="0 0 24 24" aria-hidden="true"><path d="M15 4 L7 12 L15 20" fill="none" stroke="#b5b5b5" stroke-width="2"/></svg>
    <div class="partner" style="left:88px"><span></span></div>
    <div class="partner" style="left:285px"><span></span></div>
    <div class="partner" style="left:483px"><span></span></div>
    <div class="partner" style="left:680px"><span></span></div>
    <svg class="arrow" style="left:873px" viewBox="0 0 24 24" aria-hidden="true"><path d="M9 4 L17 12 L9 20" fill="none" stroke="#b5b5b5" stroke-width="2"/></svg>
  </section>

  <footer class="footer">© 2016 LICHTWERK IT SOLUTIONS. All Rights Reserved.</footer>
</div>
</body>
</html>
```